Sustainably Transforming Education

Company is education services based. early learning through adult and corporate. Focus is national government policy and program design and delivery alongside a research based and academically grounded set of approaches to planning, evaluation, and change management.I am looking for an innovative design position that aligns with the global agendas for innovation, creativity and collaboration at international and national policy levels (berulo is a name that reflects these qualities - colours need to reflect amythyst in some way). I also need a design that translates from a business card as 1 medium of interaction to a template that can work in word/powerpoint etc to support both stationery as well as a digital strategy across multiple channels (fb/twit/etc)There is no slogan/tag line for the company and their is no logo. I was looking to just leverage the name - have currently played around with various fonts (ending up with cuisine - all lowercase).

Industry/Entity Type

Adult

Contact Information for Business Card

name: berulo (all lowercase)Chairman: Andrew CrowMobile: +61 418 902 131Web: www.berulo.comemail: martin.pelly@berulo-example.com

Font styles to use
Script
Other font styles liked:
• cuisine

Colors
e34298
e667a6
33a6d7
aaaaaa

Requirements
Nice to have
• https://files.example-share.net/sh/qx7kw2hd91lzmnp/AAFr3tYbQeLp8VwZnKcDs2Hu?dl=0
• Link to the printwell templates used to begin this process....the one with the lines was about people intersecting (collaborating).....the organic shapes one more of a fluid feel of people coming together - the overall shape being largely spherical could represent a "global" feel.....anyway that is how I was thinking about these

```html
<!DOCTYPE html>
<html lang="en">
<head>
<meta charset="utf-8">
<title>Martin Pelly – Business Card</title>
<link rel="stylesheet" href="https://fonts.googleapis.com/css2?family=Courgette&display=swap">
<style>
  :root {
    --ink-night: #0d0a24;
    --amethyst-blue: #6a64c8;
    --amethyst-violet: #8a5fc0;
    --berulo-magenta: #e34298;
    --berulo-pink: #e667a6;
    --text-white: #ffffff;
    --icon-dark: #141020;
  }
  html, body {
    margin: 0;
    padding: 0;
    width: 1200px;
    height: 740px;
    overflow: hidden;
    background: var(--ink-night);
  }
  .card {
    position: relative;
    width: 1200px;
    height: 740px;
    overflow: hidden;
    font-family: "Courgette", cursive;
    color: var(--text-white);
  }
  .card__network {
    position: absolute;
    inset: 0;
    background:
      radial-gradient(ellipse 420px 300px at 12% 18%, rgba(106,100,200,0.75), transparent 70%),
      radial-gradient(ellipse 380px 260px at 88% 12%, rgba(227,66,152,0.55), transparent 70%),
      radial-gradient(ellipse 460px 320px at 80% 55%, rgba(138,95,192,0.7), transparent 70%),
      radial-gradient(ellipse 360px 260px at 40% 50%, rgba(230,103,166,0.45), transparent 70%),
      radial-gradient(ellipse 420px 260px at 20% 90%, rgba(106,100,200,0.7), transparent 70%),
      radial-gradient(ellipse 400px 240px at 70% 95%, rgba(227,66,152,0.55), transparent 70%),
      linear-gradient(135deg, #1b1550 0%, var(--ink-night) 50%, #2a1448 100%);
  }
  .card__name {
    position: absolute;
    right: 78px;
    top: 62px;
    margin: 0;
    font-size: 96px;
    font-weight: 400;
    line-height: 1;
    white-space: nowrap;
  }
  .card__role {
    position: absolute;
    right: 84px;
    top: 196px;
    margin: 0;
    font-size: 44px;
    font-weight: 400;
    line-height: 1;
  }
  .contact {
    position: absolute;
    left: 684px;
    top: 488px;
    margin: 0;
    padding: 0;
    list-style: none;
  }
  .contact__item {
    display: flex;
    align-items: center;
    height: 44px;
    font-size: 25px;
    white-space: nowrap;
  }
  .contact__icon {
    width: 26px;
    height: 26px;
    margin-right: 36px;
    flex: none;
  }
  .contact__icon * {
    fill: none;
    stroke: var(--icon-dark);
    stroke-width: 2;
  }
  .contact__icon .solid { fill: var(--icon-dark); stroke: none; }
</style>
</head>
<body>
  <main class="card">
    <div class="card__network" role="img" aria-label="Abstract network of intersecting blue, violet and magenta lines representing people collaborating"></div>

    <h1 class="card__name">Martin Pelly</h1>
    <p class="card__role">Chairman</p>

    <ul class="contact">
      <li class="contact__item">
        <svg class="contact__icon" viewBox="0 0 26 26" aria-hidden="true">
          <path class="solid" d="M3 9c0-3 4-5 10-5s10 2 10 5v2h-5V9c-1-1-3-1-5-1s-4 0-5 1v2H3z"/>
          <path class="solid" d="M6 13h14l3 9H3z"/>
        </svg>
        <span>+61 427 315 086</span>
      </li>
      <li class="contact__item">
        <svg class="contact__icon" viewBox="0 0 26 26" aria-hidden="true">
          <rect class="solid" x="2" y="6" width="22" height="15"/>
          <path d="M2 6l11 9 11-9" style="stroke:#6a64c8"/>
        </svg>
        <span>martin.pelly@berulo-example.com</span>
      </li>
      <li class="contact__item">
        <svg class="contact__icon" viewBox="0 0 26 26" aria-hidden="true">
          <circle cx="13" cy="13" r="11"/>
          <ellipse cx="13" cy="13" rx="5" ry="11"/>
          <path d="M2 13h22M4 7h18M4 19h18"/>
        </svg>
        <span>www.berulo-example.com</span>
      </li>
    </ul>
  </main>
</body>
</html>
```